Billboard design for dentist that sees only children

I own a 12' x 25' digital billboard and I need help with billboard design. My wife is a general dentist that only sees children and is very passionate about giving them a quality dental experience . She has a great reputation in town. Obviously with a billboard there can't be a lot of reading. Maybe something that shows safety, love, experience and children. I am completely open to your ideas. In addition I have other businesses that also need billboard design so this could lead to more work. If you go to Maplecovedental.com under the about section you will find more information about the practice and our phone number. Attached is our logo which could be changed and content specs for the digital billboard. Happy Designing!!

Target Market(s)

Parents with children

Colors

Designer to choose colors to be used in the design.

Requirements
Must have
• Must attract attention and be nice to look at.
Nice to have
• Probably should have children in the picture ..... Maybe
Should not have
• If I see something I don't like I will let you know

```html
<!DOCTYPE html>
<html lang="en">
<head>
<meta charset="utf-8">
<title>Maple Cove Dental – Billboard</title>
<link rel="stylesheet" href="https://fonts.googleapis.com/css2?family=Open+Sans:ital,wght@0,400;0,600;0,700;1,400&family=Open+Sans+Condensed:wght@700&display=swap">
<style>
  :root {
    --backdrop: #bcbdbf;
    --paper: #f3f3f3;
    --green-deep: #2b5f55;
    --green-mid: #3f8a78;
    --green-soft: #4f8c80;
    --teal-title: #2f8a72;
    --sky-tag: #2a9ad8;
    --contact-rim: #e6e6e6;
    --white: #ffffff;
  }
  html, body {
    margin: 0;
    padding: 0;
    width: 1200px;
    height: 702px;
    overflow: hidden;
    background: var(--backdrop);
  }
  .billboard {
    position: absolute;
    left: 82px;
    top: 91px;
    width: 1029px;
    height: 489px;
    background: var(--paper);
    overflow: hidden;
  }
  .billboard svg {
    display: block;
    width: 1029px;
    height: 489px;
  }
  .brand-name {
    font-family: "Open Sans", sans-serif;
    font-weight: 600;
    font-size: 70px;
    fill: var(--teal-title);
  }
  .brand-tagline {
    font-family: "Open Sans", sans-serif;
    font-style: italic;
    font-weight: 400;
    font-size: 33px;
    fill: var(--sky-tag);
  }
  .badge-text {
    font-family: "Open Sans Condensed", "Open Sans", sans-serif;
    font-weight: 700;
    font-size: 21px;
    fill: var(--white);
  }
  .phone {
    font-family: "Open Sans", sans-serif;
    font-weight: 700;
    font-size: 31px;
    letter-spacing: 4px;
    fill: var(--white);
  }
  .address {
    font-family: "Open Sans", sans-serif;
    font-weight: 400;
    font-size: 17px;
    fill: var(--white);
  }
</style>
</head>
<body>
  <div class="billboard">
    <svg viewBox="0 0 1029 489" xmlns="http://www.w3.org/2000/svg">
      <defs>
        <linearGradient id="photoTone" x1="0" y1="0.2" x2="1" y2="0.8">
          <stop offset="0" stop-color="#e6eef4"/>
          <stop offset="0.14" stop-color="#efd6c4"/>
          <stop offset="0.28" stop-color="#e2c9a8"/>
          <stop offset="0.42" stop-color="#b8cc86"/>
          <stop offset="0.58" stop-color="#f0c6cc"/>
          <stop offset="0.72" stop-color="#e7b79d"/>
          <stop offset="0.84" stop-color="#a97c64"/>
          <stop offset="1" stop-color="#eef4f8"/>
        </linearGradient>
      </defs>

      <!-- header: brand -->
      <g class="brand">
        <circle cx="254" cy="58" r="15" fill="var(--teal-title)"/>
        <text class="brand-name" x="284" y="84" textLength="622">Maple Cove Dental</text>
        <text class="brand-tagline" x="481" y="117" textLength="424">general dentistry for children</text>
      </g>

      <!-- photo of four excited children -->
      <g role="img" aria-label="Photo of four excited young children lying down side by side, hands on cheeks, smiling with open mouths">
        <path d="M0,262 Q480,130 1029,176 L1029,489 L0,489 Z" fill="url(#photoTone)"/>
      </g>

      <!-- header swoosh bands -->
      <path class="swoosh-main" d="M0,214 Q470,100 1029,167 L1029,175 Q470,118 0,246 Z" fill="var(--green-deep)"/>
      <path class="swoosh-light" d="M0,248 Q470,124 1029,177 L1029,180 Q470,134 0,262 Z" fill="var(--green-mid)"/>

      <!-- call-to-action badge -->
      <g class="badge">
        <circle cx="89" cy="407" r="76" fill="var(--white)"/>
        <circle cx="89" cy="407" r="73" fill="var(--green-soft)"/>
        <text class="badge-text" text-anchor="middle" x="89" y="380">IT IS TIME</text>
        <text class="badge-text" text-anchor="middle" x="89" y="408">TO SEE YOUR</text>
        <text class="badge-text" text-anchor="middle" x="89" y="436">DENTIST?</text>
      </g>

      <!-- contact panel -->
      <g class="contact">
        <path d="M510,489 Q700,370 1029,384 L1029,489 Z" fill="var(--contact-rim)"/>
        <path d="M524,489 Q710,382 1029,392 L1029,489 Z" fill="var(--green-deep)"/>
        <g class="phone-icon" fill="none" stroke="var(--white)" stroke-width="2.4">
          <circle cx="728" cy="425" r="13"/>
          <path d="M722,418 q-2,3 1,8 q4,6 9,7 l3,-3 l-4,-3 l-2,2 q-3,-2 -5,-5 l2,-2 l-3,-4 Z" fill="var(--white)" stroke-width="1"/>
        </g>
        <text class="phone" x="759" y="437">555 014 2086</text>
        <text class="address" x="622" y="469" textLength="388">428 North Birchwood Lane Fairhaven, NM 88001</text>
      </g>
    </svg>
  </div>
</body>
</html>
```